Plakat-Design für Immobilienmakler und Baufinanzierer
Zielgruppe
Wir sind Immobilienmakler und Baufinanzierer und suchen ein hochwertiges Design, unsere Zielgruppe sind Kunden, die Ihr Haus verkaufen möchten. Für jeden erfolgreichen Verkauf spenden wir 5 % unserer Maklercourtage an einen Verein, den sich der Kunde aussuchen darf. Mit diesem Plakat wollen wir auf unsere Vereinsförderng aufmerksam machen und Vereine ansprechen.
Aufgabenstellung
Text: 'Wir spenden 5 % unserer Provision für Ihren Verein', 'Nur 1,99 % Maklercourtage', Logo, Kontaktdaten

```html
<!DOCTYPE html>
<html lang="de">
<head>
<meta charset="utf-8">
<title>Harlenbek Immobilien – Vereinsförderung</title>
<link rel="stylesheet" href="https://fonts.googleapis.com/css2?family=Montserrat:wght@500;600;700&family=Raleway:wght@500;600;700;800;900&display=swap">
<style>
  :root {
    --teal: #177386;
    --grey: #959595;
    --white: #ffffff;
    --text-grey: #545454;
    --stage: #dcdcdc;
    --sky: #4a8ccf;
    --facade: #c9bcae;
    --road: #d8d2c8;
  }
  * { margin: 0; padding: 0; box-sizing: border-box; }
  html, body { width: 1200px; height: 1177px; overflow: hidden; background: var(--stage); }
  .poster {
    position: absolute;
    left: 194px; top: 23px;
    width: 1226px; height: 1706px;
    background: var(--white);
    transform: scale(0.6624);
    transform-origin: 0 0;
    overflow: hidden;
    box-shadow: 0 10px 40px rgba(0,0,0,.18);
    font-variant-numeric: lining-nums;
    font-feature-settings: "lnum" 1;
  }
  .shapes { position: absolute; inset: 0; }
  .txt { position: absolute; line-height: 1; white-space: nowrap; }
  .brand {
    left: 548px; top: 214px; width: 562px; text-align: center;
    font-family: "Montserrat", sans-serif; font-weight: 600;
    font-size: 40px; letter-spacing: 3px; color: var(--teal);
  }
  .brand-rule { position: absolute; left: 555px; top: 271px; width: 547px; height: 2px; background: var(--grey); }
  .tagline {
    left: 548px; top: 282px; width: 562px; text-align: center;
    font-family: "Montserrat", sans-serif; font-weight: 500;
    font-size: 14px; letter-spacing: 9px; color: var(--text-grey);
  }
  .head-lead { left: 92px; top: 398px; font-family: "Raleway", sans-serif; font-weight: 800; font-size: 90px; color: var(--white); }
  .head-figure { left: 70px; top: 458px; font-family: "Raleway", sans-serif; font-weight: 900; font-size: 400px; color: var(--white); letter-spacing: -8px; }
  .head-unserer { left: 72px; top: 812px; font-family: "Raleway", sans-serif; font-weight: 800; font-size: 84px; color: var(--white); }
  .head-provision { left: 72px; top: 890px; font-family: "Raleway", sans-serif; font-weight: 800; font-size: 86px; color: var(--white); }
  .head-verein { left: 72px; top: 981px; font-family: "Raleway", sans-serif; font-weight: 500; font-size: 42px; color: var(--white); }
  .offer { left: 752px; width: 410px; text-align: center; font-family: "Raleway", sans-serif; color: var(--teal); }
  .offer-nur { top: 1135px; font-size: 88px; font-weight: 600; }
  .offer-rate { top: 1208px; font-size: 152px; font-weight: 900; letter-spacing: -3px; }
  .offer-label { top: 1367px; font-size: 44px; font-weight: 700; }
  .contact-name { left: 79px; top: 1481px; font-family: "Montserrat", sans-serif; font-weight: 700; font-size: 24px; color: var(--teal); }
  .contact-line { position: absolute; display: flex; align-items: center; gap: 18px; font-family: "Montserrat", sans-serif; font-weight: 500; font-size: 25px; color: var(--text-grey); white-space: nowrap; }
  .contact-line svg { width: 28px; height: 28px; flex: none; }
</style>
</head>
<body>
<div class="poster">
  <svg class="shapes" viewBox="0 0 1226 1706" width="1226" height="1706">
    <defs>
      <linearGradient id="scene" x1="0" y1="0" x2="0" y2="1">
        <stop offset="0" stop-color="var(--sky)"/>
        <stop offset="0.3" stop-color="#7fb0dc"/>
        <stop offset="0.42" stop-color="var(--facade)"/>
        <stop offset="0.72" stop-color="#b3a593"/>
        <stop offset="0.8" stop-color="#8faa6a"/>
        <stop offset="0.84" stop-color="var(--road)"/>
        <stop offset="1" stop-color="#e4e0d8"/>
      </linearGradient>
    </defs>
    <polygon class="band-teal" points="0,107 937,492 0,1420" fill="var(--teal)"/>
    <polygon class="band-grey" points="1006,500 1226,408 1226,690" fill="var(--grey)"/>
    <g role="img" aria-label="Foto einer Reihe moderner Stadthäuser an einer Straße unter blauem Himmel">
      <polygon points="961,515 961,1005 530,1420 53,1420" fill="url(#scene)"/>
      <polygon points="985,515 1226,709 1226,1226 985,993" fill="url(#scene)"/>
    </g>
    <polygon class="corner-teal" points="1226,1342 836,1706 1226,1706" fill="var(--teal)"/>
  </svg>

  <div class="txt brand">HARLENBEK IMMOBILIEN</div>
  <div class="brand-rule"></div>
  <div class="txt tagline">IMMOBILIEN &amp; BAUFINANZIERUNG</div>

  <div class="txt head-lead">Wir spenden</div>
  <div class="txt head-figure">5%</div>
  <div class="txt head-unserer">unserer</div>
  <div class="txt head-provision">Provision</div>
  <div class="txt head-verein">für Ihren Verein</div>

  <div class="txt offer offer-nur">Nur</div>
  <div class="txt offer offer-rate">1,99%</div>
  <div class="txt offer offer-label">Maklercourtage</div>

  <div class="txt contact-name">HARLENBEK IMMOBILIEN</div>
  <div class="contact-line" style="left:79px;top:1524px">
    <svg viewBox="0 0 24 24"><path d="M12 2a7 7 0 0 0-7 7c0 5 7 13 7 13s7-8 7-13a7 7 0 0 0-7-7z" fill="var(--teal)"/><circle cx="12" cy="9" r="2.6" fill="#fff"/></svg>
    <span>LINDENWEG 12 41236 MÖNCHSFELD</span>
  </div>
  <div class="contact-line" style="left:79px;top:1580px">
    <svg viewBox="0 0 24 24"><circle cx="12" cy="12" r="11" fill="var(--teal)"/><path d="M8.5 6.5l2 2.2-1.2 1.6c.8 1.7 2 2.9 3.7 3.8l1.6-1.2 2.2 2-1.4 2c-4.4-.6-8.2-4.4-8.7-8.8z" fill="#fff"/></svg>
    <span>02173 318 20 64</span>
  </div>
  <div class="contact-line" style="left:79px;top:1635px">
    <svg viewBox="0 0 24 24"><rect x="6" y="2" width="12" height="20" rx="2" transform="rotate(-25 12 12)" fill="none" stroke="var(--teal)" stroke-width="2"/></svg>
    <span>0151 724 608 35</span>
  </div>
  <div class="contact-line" style="left:370px;top:1580px">
    <svg viewBox="0 0 24 24"><circle cx="12" cy="12" r="11" fill="var(--teal)"/><rect x="6.5" y="8" width="11" height="8" fill="none" stroke="#fff" stroke-width="1.4"/><path d="M6.5 8l5.5 4.5L17.5 8" fill="none" stroke="#fff" stroke-width="1.4"/></svg>
    <span>INFO@HARLENBEK-IMMOBILIEN.DE</span>
  </div>
  <div class="contact-line" style="left:370px;top:1635px">
    <svg viewBox="0 0 24 24"><circle cx="12" cy="12" r="11" fill="var(--teal)"/><circle cx="12" cy="12" r="6" fill="none" stroke="#fff" stroke-width="1.3"/><ellipse cx="12" cy="12" rx="2.6" ry="6" fill="none" stroke="#fff" stroke-width="1.3"/><path d="M6 12h12" stroke="#fff" stroke-width="1.3"/></svg>
    <span>WWW.HARLENBEK-IMMOBILIEN.DE</span>
  </div>
</div>
</body>
</html>
```